Revamp our wedding venue website

Currently we are using wordpress for our website and hoped to find a designer that can assist us with making the website prettier and more pleasing and draw more interest. www.velmorhall.com is our current site. We are connected to google business mail, so I would prefer to stay with this for now and update our gallery with new photos, blog page and putting the contact us form back on all the pages.

Target Market(s)

20-40 years of age, all ranges of styles and generally clients looking for a different modern feel vs. a hotel hall.

Industry/Entity Type

Wedding

Logo Text

1927 Velmor Hall

Number of Pages Required

4 page

Font styles to use
Serif

Requirements
Must have
• Light, airy feel. Romantic and informative. Mobile friendly and easy to contact us-preferred contact form on all pages. Gallery of photos. Previous reviews
Nice to have
• Bio of staff, maybe some videos, and fun things to do in the area for out of town guests. Maps and also venue blank floor plan.

```html
<!DOCTYPE html>
<html lang="en">
<head>
<meta charset="utf-8">
<title>1927 Velmor Hall — Weddings &amp; Events</title>
<link href="https://fonts.googleapis.com/css2?family=Josefin+Sans:wght@300;400;600;700&family=Open+Sans:wght@400;600&family=Merriweather:wght@300;400&display=swap" rel="stylesheet">
<style>
:root{
  --ink:#2f2f2f;
  --dark:#333333;
  --footer:#383838;
  --muted:#777777;
  --line:#dddddd;
  --white:#ffffff;
  --hero-a:#4a5148;
  --hero-b:#2e332f;
  --band-a:#7d7f86;
  --band-b:#5f5f66;
}
*{box-sizing:border-box;margin:0;padding:0}
html,body{width:1200px;height:2195px;overflow:hidden}
body{position:relative;background:var(--white);font-family:'Open Sans',sans-serif;color:var(--ink)}
.abs{position:absolute}
.center{text-align:center}

/* top bar */
.topbar{left:0;top:0;width:1200px;height:38px;background:var(--dark);color:var(--white);font-size:10px;font-family:'Josefin Sans',sans-serif}
.topbar .tagline{left:132px;top:13px;display:flex;align-items:center;gap:8px}
.topbar .contacts{right:132px;top:13px;display:flex;gap:22px}
.topbar .contacts span{display:flex;align-items:center;gap:7px}

/* header */
.header{left:0;top:38px;width:1200px;height:104px;background:var(--white)}
.brand{left:132px;top:37px;font-family:'Josefin Sans',sans-serif;font-size:30px;font-weight:600;color:var(--ink)}
.nav{right:132px;top:48px;display:flex;font-family:'Josefin Sans',sans-serif;font-size:11px;letter-spacing:1.5px;color:var(--muted)}
.nav a{color:inherit;text-decoration:none;padding:0 24px;border-left:1px solid #999;line-height:12px}
.nav a:first-child{border-left:0;color:var(--ink)}
.nav a:last-child{padding-right:0}

/* hero */
.hero{left:0;top:142px;width:1200px;height:472px;background:linear-gradient(100deg,var(--hero-a),#5d6560 55%,var(--hero-b))}
.hero .kicker{left:0;width:1200px;top:118px;font-family:'Merriweather',serif;font-weight:300;font-size:24px;color:var(--white)}
.hero .rule{left:447px;width:306px;height:2px;background:var(--white)}
.hero h1{left:0;width:1200px;top:184px;font-family:'Josefin Sans',sans-serif;font-weight:700;font-size:58px;color:var(--white);letter-spacing:1px}
.hero .sub{left:0;width:1200px;top:284px;font-family:'Merriweather',serif;font-size:15px;color:var(--white)}
.btn-consult{left:473px;top:331px;width:254px;height:54px;border-radius:27px;background:var(--dark);color:var(--white);font-family:'Josefin Sans',sans-serif;font-weight:700;font-size:14px;letter-spacing:1px;display:flex;align-items:center;justify-content:center}
.hero .arrow{top:230px}

/* services */
.section-title{left:0;width:1200px;font-family:'Josefin Sans',sans-serif;font-size:31px;letter-spacing:4px;font-weight:400;color:var(--ink)}
.card{top:797px;width:293px;height:300px;background:var(--white);box-shadow:0 2px 6px rgba(0,0,0,.22)}
.card .icon{left:92px;top:-54px;width:108px;height:108px;border-radius:50%;background:var(--dark);display:flex;align-items:center;justify-content:center}
.card h3{left:0;width:100%;top:108px;font-family:'Josefin Sans',sans-serif;font-weight:400;font-size:19px;letter-spacing:2.5px}
.card p{left:24px;width:245px;top:146px;font-size:10px;line-height:19px;color:#555}
.btn-small{left:95px;width:102px;height:32px;border-radius:16px;background:var(--dark);color:var(--white);font-size:9.5px;display:flex;align-items:center;justify-content:center}

/* testimonial */
.testimonial{left:0;top:1170px;width:1200px;height:325px;background:linear-gradient(180deg,var(--band-a),var(--band-b))}
.testimonial h2{left:0;width:1200px;top:65px;font-family:'Josefin Sans',sans-serif;font-weight:400;font-size:30px;letter-spacing:3px;color:var(--white)}
.testimonial .quote{left:132px;width:936px;top:132px;font-size:11px;line-height:20px;color:var(--white)}
.testimonial .author{left:0;width:1200px;top:198px;font-size:10px;font-style:italic;font-weight:600;color:var(--white)}
.dots{left:581px;top:246px;display:flex;gap:8px}
.dots i{width:7px;height:7px;border-radius:50%;background:rgba(255,255,255,.45)}
.dots i:first-child{background:var(--white)}

/* events */
.event{top:1624px;width:231px;height:202px}
.event-overlay{left:603px;background:#3b3b3d}
.event-overlay .frame{left:10px;top:10px;right:10px;bottom:10px;border:1px solid rgba(255,255,255,.7)}
.event-overlay h4{left:0;width:100%;top:56px;font-family:'Josefin Sans',sans-serif;font-weight:400;font-size:20px;letter-spacing:2px;color:var(--white)}
.event-overlay p{left:34px;width:163px;top:95px;font-size:10px;line-height:19px;color:var(--white)}

/* footer */
.footer{left:0;top:1876px;width:1200px;height:319px;background:var(--footer);color:var(--white)}
.footer h5{top:36px;font-family:'Josefin Sans',sans-serif;font-weight:400;font-size:15px;letter-spacing:.5px}
.footer .underline{top:69px;height:1px;background:#5a5a5a}
.footer .col{top:88px;font-size:10px;line-height:23px}
.footer .contact-row{display:flex;gap:12px;align-items:flex-start;line-height:15px;margin-bottom:12px}
.footer .contact-row u{text-decoration:underline}
.social{left:856px;top:96px;display:flex;gap:8px}
.social i{width:34px;height:34px;border:1px solid #777}
.copyright{left:0;width:1200px;top:284px;font-size:10px}
</style>
</head>
<body>

<div class="abs topbar">
  <div class="abs tagline">
    <svg width="8" height="11" viewBox="0 0 8 11"><path d="M4 0a4 4 0 0 0-4 4c0 3 4 7 4 7s4-4 4-7a4 4 0 0 0-4-4zm0 5.5A1.5 1.5 0 1 1 4 2.5a1.5 1.5 0 0 1 0 3z" fill="#fff"/></svg>
    Tampa's Most Unique Wedding and Events Venue
  </div>
  <div class="abs contacts">
    <span><svg width="10" height="10" viewBox="0 0 10 10"><path d="M2 0l2 2.5-1.2 1.3a6 6 0 0 0 3.4 3.4L7.5 6 10 8l-1.5 2C4 10 0 6 0 1.5z" fill="#fff"/></svg>813.555.0142</span>
    <span><svg width="12" height="9" viewBox="0 0 12 9"><rect x=".5" y=".5" width="11" height="8" fill="none" stroke="#fff"/><path d="M.5.5l5.5 4.5L11.5.5" fill="none" stroke="#fff"/></svg>Events@VelmorHall.com</span>
  </div>
</div>

<header class="abs header">
  <div class="abs brand">1927 Velmor Hall</div>
  <nav class="abs nav">
    <a href="#">HOME</a><a href="#">WEDDINGS</a><a href="#">EVENTS</a><a href="#">CATERING</a><a href="#">GALLERY</a><a href="#">CONTACT US</a>
  </nav>
</header>

<section class="abs hero" role="img" aria-label="Photo of a bride and groom beside a decorated white wedding car">
  <div class="abs kicker center">unique and historic venue</div>
  <div class="abs rule" style="top:166px"></div>
  <h1 class="abs center">WEDDINGS &amp; EVENTS</h1>
  <div class="abs rule" style="top:256px"></div>
  <div class="abs sub center">Imagine your wedding or event in Tampa’s premiere</div>
  <div class="abs btn-consult">SCHEDULE CONSULTATION</div>
  <svg class="abs arrow" style="left:130px" width="24" height="24" viewBox="0 0 24 24"><circle cx="12" cy="12" r="11" fill="none" stroke="#fff" stroke-width="1.3"/><path d="M14 7l-5 5 5 5" fill="none" stroke="#fff" stroke-width="1.3"/></svg>
  <svg class="abs arrow" style="left:1042px" width="24" height="24" viewBox="0 0 24 24"><circle cx="12" cy="12" r="11" fill="none" stroke="#fff" stroke-width="1.3"/><path d="M10 7l5 5-5 5" fill="none" stroke="#fff" stroke-width="1.3"/></svg>
</section>

<h2 class="abs section-title center" style="top:670px">OUR SERVICES</h2>

<div class="abs card" style="left:132px">
  <div class="abs icon"><svg width="58" height="52" viewBox="0 0 58 52"><path d="M29 52L5 28A15 15 0 0 1 29 8a15 15 0 0 1 24 20z" fill="#fff"/></svg></div>
  <h3 class="abs center">WEDDINGS</h3>
  <p class="abs center">When choosing the location for your wedding or event, the 1927 Velmor Hall provides you with an all-inclusive experience</p>
  <div class="abs btn-small" style="top:229px">READ MORE</div>
</div>
<div class="abs card" style="left:454px">
  <div class="abs icon"><svg width="50" height="54" viewBox="0 0 50 54"><path d="M2 2h46L29 26v20h10v6H11v-6h10V26z" fill="#fff"/><path d="M12 8h26L25 21z" fill="#333"/></svg></div>
  <h3 class="abs center" style="top:104px">EVENTS</h3>
  <p class="abs center" style="top:142px">When choosing the location for your wedding or event, the 1927 Velmor Hall provides you with an all-inclusive experience</p>
  <div class="abs btn-small" style="top:225px">READ MORE</div>
</div>
<div class="abs card" style="left:772px">
  <div class="abs icon"><svg width="48" height="58" viewBox="0 0 48 58"><path d="M4 0h3v16h3V0h3v16h3V0h3v18a6 6 0 0 1-5 6v34H9V24a6 6 0 0 1-5-6z" fill="#fff"/><path d="M30 0c8 0 14 8 14 22v10h-5v26h-9z" fill="#fff"/></svg></div>
  <h3 class="abs center" style="top:104px">CATERING</h3>
  <p class="abs center" style="top:142px">When choosing the location for your wedding or event, the 1927 Velmor Hall provides you with an all-inclusive experience</p>
  <div class="abs btn-small" style="top:225px">READ MORE</div>
</div>

<section class="abs testimonial" role="img" aria-label="Photo of a beach ceremony with white chairs and purple flowers">
  <h2 class="abs center">TESTIMONIAL</h2>
  <p class="abs quote center">My fiancé and I are extremely excited to start planning our wedding at this amazing venue! Marisol and the rest of the staff have been very...Perfection! My husband and I just got married this past weekend and we were so fortunate that the 1927 Velmor Hall hosted our...</p>
  <div class="abs author center">- JOHN DOE -</div>
  <div class="abs dots"><i></i><i></i><i></i></div>
</section>

<h2 class="abs section-title center" style="top:1548px">RECENT EVENTS</h2>
<svg class="abs" style="left:101px;top:1718px" width="10" height="16" viewBox="0 0 10 16"><path d="M8 1L2 8l6 7" fill="none" stroke="#444" stroke-width="1.5"/></svg>
<div class="abs event" style="left:132px;background:linear-gradient(160deg,#6b5a4e,#2f2a2a)" role="img" aria-label="Photo of a model on a runway at a fashion show"></div>
<div class="abs event" style="left:367px;background:linear-gradient(180deg,#8a8f93,#4d4a4a)" role="img" aria-label="Photo of a crowded seated audience at an event"></div>
<div class="abs event event-overlay">
  <div class="abs frame"></div>
  <h4 class="abs center">LOREM IPSUM</h4>
  <p class="abs center">Words can't express the simple perfection of the night that they were able to provide.</p>
</div>
<div class="abs event" style="left:838px;background:linear-gradient(150deg,#3a3f9e,#161533 70%)" role="img" aria-label="Photo of a party under blue and purple lights"></div>
<svg class="abs" style="left:1086px;top:1718px" width="10" height="16" viewBox="0 0 10 16"><path d="M2 1l6 7-6 7" fill="none" stroke="#444" stroke-width="1.5"/></svg>

<footer class="abs footer">
  <h5 class="abs" style="left:132px">ABOUT US</h5>
  <div class="abs underline" style="left:132px;width:210px"></div>
  <div class="abs col" style="left:132px;width:220px">Have questions? Want to come and see the<br>1927 Velmor Hall for yourselves?<br>Call or contact</div>

  <h5 class="abs" style="left:373px">QUICK LINKS</h5>
  <div class="abs underline" style="left:373px;width:210px"></div>
  <div class="abs col" style="left:373px">About<br>Weddings<br>Events<br>Catering<br>Gallery<br>Contact Us</div>

  <h5 class="abs" style="left:610px">CONTACT US</h5>
  <div class="abs underline" style="left:610px;width:215px"></div>
  <div class="abs col" style="left:610px;top:96px">
    <div class="contact-row"><svg width="12" height="11" viewBox="0 0 12 11"><path d="M0 3c0-2 3-3 6-3s6 1 6 3v1H9V2.5H3V4H0zM2 5h8l1 6H1z" fill="#fff"/></svg>813.555.0142</div>
    <div class="contact-row"><svg width="12" height="11" viewBox="0 0 12 11"><rect x="3" y="0" width="6" height="3" fill="#fff"/><rect x="0" y="4" width="12" height="5" fill="#fff"/><rect x="3" y="7" width="6" height="4" fill="#fff" stroke="#383838"/></svg>813.555.0142</div>
    <div class="contact-row"><svg width="12" height="9" viewBox="0 0 12 9"><rect width="12" height="9" fill="#fff"/><path d="M0 0l6 5 6-5" fill="none" stroke="#383838"/></svg><u>Events@VelmorHall.com</u></div>
    <div class="contact-row"><svg width="12" height="13" viewBox="0 0 8 11"><path d="M4 0a4 4 0 0 0-4 4c0 3 4 7 4 7s4-4 4-7a4 4 0 0 0-4-4zm0 5.5A1.5 1.5 0 1 1 4 2.5a1.5 1.5 0 0 1 0 3z" fill="#fff"/></svg><span>1927 North Harbor Ave. Tampa,<br>FL 33602</span></div>
  </div>

  <h5 class="abs" style="left:856px">FOLLOW US</h5>
  <div class="abs underline" style="left:856px;width:212px"></div>
  <div class="abs social"><i></i><i></i><i></i><i></i></div>

  <div class="abs copyright center">Copyright © 2016 velmorhall.com. All right Reserved.</div>
</footer>

</body>
</html>
```